Doctor business card, bold, modern, stand out, keep worthy

I'm a specialist doctor (Oncology and hematology) and I need a flashy business card to hand out to other doctors. I am looking for something that stands out, either with embossing or transparency or high quality paper. I want my card not to look or feel generic. I'm a hematology oncology specialist, and somewhere on the card I should incorporate the TLVB logo, along with my name, my title (hematology/oncology) and board certifications (in oncology and internal medicine), finally with our practice address (82 Orchard Ave Suite 4 Edison NJ 08815) and tel and fax numbers

Target Market(s)

other doctors, patients

Industry/Entity Type

Healthcare

Contact Information for Business Card

1. my name 2. Job title (hematology/Oncology) 3. credentials (Board Certified Medical Oncology/Board Certified Internal Medicine) 4. Address 5. Phone and Fax Number

Font styles to use
Serif

Colors

Designer to choose colors to be used in the design.

Requirements
Nice to have
• flip side can have logo and date of appt blank line. Blue green colors but can vary

```html
<!DOCTYPE html>
<html lang="en">
<head>
<meta charset="utf-8">
<title>TLVB – Business Card</title>
<link rel="stylesheet" href="https://fonts.googleapis.com/css2?family=Open+Sans:wght@400;600;700&display=swap">
<style>
  :root {
    --stage: #232323;
    --card: #1d1d20;
    --card-edge: #1fb4df;
    --cyan: #22b0d8;
    --magenta: #a0379a;
    --white: #f2f2f2;
    --rule: #bdbdbd;
    --pattern-dark: #111113;
    --pattern-light: #8a8a8d;
  }
  * { margin: 0; padding: 0; box-sizing: border-box; }
  html, body {
    width: 1200px; height: 780px; overflow: hidden;
    background: var(--stage);
    font-family: "Open Sans", Arial, sans-serif;
  }
  .canvas { position: relative; width: 1200px; height: 780px; }

  .card {
    position: absolute;
    width: 560px; height: 320px;
    border-radius: 22px;
    background: var(--card);
    border-left: 4px solid var(--card-edge);
    border-bottom: 5px solid var(--card-edge);
    overflow: hidden;
    box-shadow: 0 14px 30px rgba(0,0,0,.55);
  }
  .card--back { left: 40px; top: 60px; }
  .card--front { left: 600px; top: 390px; }

  /* back side */
  .leaf-pattern {
    position: absolute; inset: 0;
    background: linear-gradient(200deg, var(--pattern-light) 0%, #3a3a3e 30%, var(--pattern-dark) 55%, #161618 100%);
    opacity: .9;
  }
  .brand {
    position: absolute; left: 26px; top: 24px;
    display: flex; align-items: center; gap: 10px;
  }
  .brand__dot {
    width: 14px; height: 14px; border-radius: 50%;
    background: var(--cyan);
  }
  .brand__name {
    font-size: 34px; font-weight: 400; letter-spacing: 4px;
    color: var(--cyan); line-height: 1;
  }
  .credentials {
    position: absolute; left: 26px; right: 20px; bottom: 26px;
    color: var(--white); font-size: 16px; font-weight: 400; letter-spacing: .3px;
  }

  /* front side */
  .identity {
    position: absolute; left: 40px; top: 116px;
  }
  .identity__name {
    font-size: 32px; font-weight: 700; line-height: 1.1; letter-spacing: .5px;
  }
  .identity__first { color: var(--cyan); }
  .identity__last { color: var(--magenta); }
  .identity__title {
    margin-top: 4px; padding-left: 46px;
    color: var(--white); font-size: 16px; font-weight: 600;
  }
  .divider {
    position: absolute; left: 300px; top: 70px;
    width: 1px; height: 130px; background: var(--rule);
  }
  .contacts {
    position: absolute; left: 318px; top: 76px;
    list-style: none;
  }
  .contacts li {
    display: flex; align-items: center; gap: 10px;
    color: var(--white); font-size: 15px; line-height: 29px;
  }
  .contacts svg { width: 16px; height: 16px; fill: var(--cyan); flex: none; }
  .address {
    position: absolute; left: 180px; bottom: 40px;
    color: var(--white); font-size: 16px; letter-spacing: .3px;
  }
</style>
</head>
<body>
<main class="canvas">

  <section class="card card--back" aria-label="Card back">
    <div class="leaf-pattern" role="img" aria-label="Repeating leaf pattern in black and silver gloss"></div>
    <div class="brand">
      <span class="brand__dot"></span>
      <span class="brand__name">TLVB</span>
    </div>
    <p class="credentials">Board Certified Medical Oncology/Board Certified Internal Medicine</p>
  </section>

  <section class="card card--front" aria-label="Card front">
    <div class="identity">
      <h1 class="identity__name"><span class="identity__first">Lena</span> <span class="identity__last">Marovic</span></h1>
      <p class="identity__title">Hematology/Oncology</p>
    </div>

    <div class="divider"></div>

    <ul class="contacts">
      <li>
        <svg viewBox="0 0 24 24" aria-hidden="true"><path d="M6.6 10.8a15 15 0 0 0 6.6 6.6l2.2-2.2c.3-.3.7-.4 1-.2 1.1.4 2.3.6 3.6.6.6 0 1 .4 1 1V20c0 .6-.4 1-1 1A17 17 0 0 1 3 4c0-.6.4-1 1-1h3.5c.6 0 1 .4 1 1 0 1.3.2 2.5.6 3.6.1.3 0 .7-.2 1z"/></svg>
        (844) 555-0172
      </li>
      <li>
        <svg viewBox="0 0 24 24" aria-hidden="true"><path d="M7 3h9l3 3v4H7zM4 10h16a2 2 0 0 1 2 2v7a2 2 0 0 1-2 2H4a2 2 0 0 1-2-2v-7a2 2 0 0 1 2-2zm3 3v2h2v-2zm4 0v2h2v-2zm4 0v2h2v-2zm-8 4v2h2v-2zm4 0v2h2v-2z"/></svg>
        (844) 555-0173
      </li>
      <li>
        <svg viewBox="0 0 24 24" aria-hidden="true"><path d="M2 5h20v14H2zm2 2v.5l8 5 8-5V7zm0 2.8V17h16V9.8l-8 5z"/></svg>
        info@tlvbcare.org
      </li>
      <li>
        <svg viewBox="0 0 24 24" aria-hidden="true"><path d="M12 2a10 10 0 1 0 0 20 10 10 0 0 0 0-20zm6.9 9h-3a15 15 0 0 0-1.2-5.6A8 8 0 0 1 18.9 11zM12 4c.9 1.2 1.8 3.6 1.9 7h-3.8c.1-3.4 1-5.8 1.9-7zM9.3 5.4A15 15 0 0 0 8.1 11h-3a8 8 0 0 1 4.2-5.6zM5.1 13h3a15 15 0 0 0 1.2 5.6A8 8 0 0 1 5.1 13zM12 20c-.9-1.2-1.8-3.6-1.9-7h3.8c-.1 3.4-1 5.8-1.9 7zm2.7-1.4a15 15 0 0 0 1.2-5.6h3a8 8 0 0 1-4.2 5.6z"/></svg>
        www.tlvbcare.org
      </li>
    </ul>

    <p class="address">82 Orchard Ave Suite 4 Edison NJ 08815</p>
  </section>

</main>
</body>
</html>
```